E-Book-Cover für einen Kriminalroman
Zielgruppe
Ich veröffentliche meinen Roman “Die Schwelle” als E-Book.
Das Buch spielt in einer nahen Zukunft, in der Die Schwelle Nachrichten in die Vergangenheit möglich macht. Unfälle und Straftaten werden sofort ungeschehen gemacht. Jeder Bürger kann seinem vergangenen Ich eine Botschaft schicken - und so die eigene Geschichte “reparieren”. Auch Henrik, ein unscheinbarer Projektleiter, erhält eines Tag eine Nachricht aus der Zukunft: 'Halte dich von Maren fern. Sie wird dein Untergang sein'. Die Nachricht stellt Henrik vor ein Rätsel. Vor welcher Gefahr hat er sich gewarnt? Und wer ist Maren? Ein Jahr später wird Henrik durch Zufall Mitwisser einer politischen Verschwörung. Die Killer machen Jagd auf ihn und kennen jeden seiner nächsten Schritte. Die letzte Rettung ist ausgerechnet eine Frau namens Maren.
--- “Die Schwelle” spielt in der Zukunft, ist aber kein Science Fiction Roman. Die beschriebene Welt ist (außer der Zeitmanipulation) wie die unsere. Am ehesten ist das Buch also ein actionreicher Kriminalroman.
Die Hauptzielgruppe sind 25 - 45-jährige, zum Beispiel Leser von Rolf Ebenhöch, Tobias Wendrath oder Karl Vossberg.
Aufgabenstellung
Gewünscht ist ein E-Book-Cover für die Verwendung auf Online-Plattformen wie Kaufora.
Autor: K.J. Brandau
Titel: Die Schwelle
Zusatz: Roman
Visuelle Anforderungen
Das Cover sollte eine Reihe von Türen zeigen. Begründung dazu: Im sogenannten Registerbüro muss der Protagonist in einer von vier nebeneinanderliegenden Türen treten und empfängt dort seine Nachricht aus der Zukunft. Das Thema “Entscheidungen fürs Leben” des Romans wird durch diese Türen visualisiert und als Symbol mehrmals aufgegriffen - dementsprechend ist es aus meiner Sicht perfekt für das Cover.
Für die Fotosuche: Das Registerbüro ist leicht heruntergekommen und wirkt kühl und unsympathisch. Dieses Bild https://de.bildquelle-beispiel.de/id/19384726 (auch noch einmal angehängt) zum Beispiel passt sehr gut.
Thema Hacking und Programmieren
Das Buch spielt in den Lebenswelten von Programmierern und Hackern; Die Schwelle ist eine Datenbank. Dies könnte durch Stil der Schrift oder anders unterstützt werden. Nur, wenn sinnvoll und ohne dass es wie ein Computerbuch aus den 90ern wirkt natürlich :)
- Die Font kann das Thema aufgreifen, aber bitte KEINE Vintage LED-Schrift im Stil von http://www.schriftkiste-beispiel.de/segment-alt.font, sondern eine die einem modernen Monitor entspringt. Entweder verpixelt (Beispiel im Anhang) oder durch eine gepunktete Schrift in hoher "Auflösung" (Beispiel: http://www.schriftkiste-beispiel.de/perlen-raster.font, also nicht nur 7 Punkte in der Breite), hier könnte man die Ränder auch etwas blurren, um den Effekt eines Monitors zu erzielen
- Wenn der o.g. Schriftstil benutzt wird, bitte in Kleinbuchstaben (wie ein Befehl auf dem Terminal)
-> All kein Muss, nur wenn sinnvoll!
Weitere Anforderungen:
- Die Türen befinden sich in einem kühlen, sterilen BÜRO, dementsprechend dürfen sie nicht zu hübsch aussehen oder an Wohnzimmertüren erinnern
- Wenn Codezeilen als Hintergrundbestandteil genutzt..

```html
<!DOCTYPE html>
<html lang="de">
<head>
<meta charset="utf-8">
<title>Die Schwelle – K.J. Brandau</title>
<link rel="stylesheet" href="https://fonts.googleapis.com/css2?family=Courier+Prime&family=Cousine&family=Oswald:wght@400&display=swap">
<style>
  :root {
    --wall-light: #c5ccc8;
    --wall-mid: #aeb7b2;
    --wall-low: #9ba49f;
    --wall-shadow: #8a938f;
    --floor-dark: #4f5552;
    --floor-mid: #6f7773;
    --floor-light: #9aa29e;
    --door-light: #f1f3f2;
    --door-mid: #d9dedb;
    --door-frame: #e3e7e5;
    --door-fade: #6a716d;
    --author-ink: #3d3f3f;
    --title-ink: #ffffff;
    --label-ink: #f2f4f3;
  }
  html, body {
    margin: 0;
    padding: 0;
    width: 768px;
    height: 1200px;
    overflow: hidden;
    background: var(--wall-light);
  }
  .cover {
    position: relative;
    width: 768px;
    height: 1200px;
    overflow: hidden;
  }
  .cover-scene {
    position: absolute;
    inset: 0;
    background: linear-gradient(
      to bottom,
      var(--wall-light) 0%,
      var(--wall-mid) 40%,
      var(--wall-low) 52%,
      var(--wall-shadow) 78%,
      var(--floor-dark) 82%,
      var(--floor-dark) 85%,
      var(--floor-mid) 90%,
      var(--floor-light) 100%
    );
  }
  .door {
    position: absolute;
    top: 624px;
    width: 171px;
    height: 360px;
    box-sizing: border-box;
    border: 6px solid var(--door-frame);
    border-bottom: none;
    background: linear-gradient(
      to bottom,
      var(--door-light) 0%,
      var(--door-mid) 78%,
      var(--door-fade) 100%
    );
  }
  .door-left { left: 32px; }
  .door-middle { left: 298px; }
  .door-right { left: 564px; }
  .author {
    position: absolute;
    top: 20px;
    left: 0;
    right: 0;
    margin: 0;
    text-align: center;
    font-family: "Courier Prime", "Courier New", monospace;
    font-weight: 400;
    font-size: 78px;
    line-height: 1;
    color: var(--author-ink);
    letter-spacing: 1px;
  }
  .title {
    position: absolute;
    top: 0;
    left: 0;
    right: 0;
    margin: 0;
    text-align: center;
    font-family: "Cousine", "Courier New", monospace;
    font-weight: 400;
    color: var(--title-ink);
    text-shadow: 3px 4px 6px rgba(0, 0, 0, 0.35);
    line-height: 1;
  }
  .title-line { display: block; }
  .title-article {
    font-size: 112px;
    margin-top: 232px;
    padding-left: 10px;
  }
  .title-word {
    font-size: 152px;
    margin-top: 2px;
    letter-spacing: -2px;
  }
  .genre {
    position: absolute;
    bottom: 42px;
    left: 0;
    right: 0;
    margin: 0;
    text-align: center;
    font-family: "Oswald", "Arial Narrow", sans-serif;
    font-weight: 400;
    font-size: 42px;
    line-height: 1;
    color: var(--label-ink);
    transform: scaleX(0.9);
  }
</style>
</head>
<body>
  <main class="cover">
    <div class="cover-scene" role="img" aria-label="Foto: kühler, verwitterter grauer Büroraum über einem dunklen Betonboden"></div>
    <div class="door door-left" role="img" aria-label="Foto: schlichte weiße Bürotür mit Türklinke"></div>
    <div class="door door-middle" role="img" aria-label="Foto: schlichte weiße Bürotür mit Türklinke"></div>
    <div class="door door-right" role="img" aria-label="Foto: schlichte weiße Bürotür mit Türklinke"></div>
    <p class="author">K.J. Brandau</p>
    <h1 class="title">
      <span class="title-line title-article">Die</span>
      <span class="title-line title-word">Schwelle</span>
    </h1>
    <p class="genre">ROMAN</p>
  </main>
</body>
</html>
```